Building Design company needing a letterhead

We need a letter head for our Building Design company to send letters etc. to our clients, consultants, councils etc. We would like to see our logo used and company colours. I have attached our style guide and an example of our current letterheads. Top left we would like our logo, top right we would like the company details and at the footer we would like some sort of image/design etc. that suits our brand. I like the Tarrow Design letterhead attached.

Target Market(s)

Professionals, Councils, Consultants, Mums & Dads

Industry/Entity Type

Architecture

Other font styles liked:
• refer the design style guide

Colors
f37122
000000
1b1b1b

Requirements
Must have
• Must have the minimum of a logo, company details and footer
Nice to have
• An image/design made for the footer that would suite our brand and website at www.corvanplans.com.au. Also it would be nice to include the KMEOT logo somewhere perhaps included in the footer.
Should not have
• Large images in the header. I just want the logo and company details.

```html
<!DOCTYPE html>
<html lang="en">
<head>
<meta charset="utf-8">
<title>Lintel Design Letterhead</title>
<link href="https://fonts.googleapis.com/css2?family=Titillium+Web:wght@600&family=Questrial&display=swap" rel="stylesheet">
<style>
  :root {
    --backdrop: #878787;
    --paper: #ffffff;
    --rule: #d6d6d6;
    --ink: #1b1b1b;
    --accent: #f37122;
    --accent-faint: #fbece7;
  }
  * { box-sizing: border-box; margin: 0; padding: 0; }
  html, body {
    width: 847px; height: 1200px; overflow: hidden;
    background: var(--backdrop);
  }
  .letterhead {
    position: absolute; left: 70px; top: 70px;
    width: 708px; height: 1059px;
    background: var(--paper);
    border: 1px solid #cfcfcf;
  }
  .brand {
    position: absolute; left: 20px; top: 30px;
    display: flex; align-items: center; gap: 14px;
  }
  .brand-square { width: 46px; height: 46px; background: var(--accent); }
  .brand-name {
    font-family: "Titillium Web", sans-serif; font-weight: 600;
    font-size: 27px; line-height: 26px; letter-spacing: 1px;
    color: var(--ink); text-transform: uppercase;
  }
  .contact {
    position: absolute; right: 24px; top: 20px;
    text-align: right;
    font-family: "Questrial", sans-serif;
    font-variant: small-caps; letter-spacing: 1.6px;
    color: var(--ink);
  }
  .contact-name { color: var(--accent); font-size: 12.5px; line-height: 14px; padding-right: 10px; }
  .contact-role { font-size: 11px; line-height: 14px; padding-right: 10px; margin-bottom: 9px; }
  .contact-line {
    display: flex; justify-content: flex-end; align-items: center; gap: 8px;
    font-size: 11px; line-height: 17px;
  }
  .contact-line svg { width: 10px; height: 10px; }
  .header-rule, .footer-rule {
    position: absolute; left: 0; right: 0; height: 1px; background: var(--rule);
  }
  .header-rule { top: 108px; }
  .footer-rule { top: 994px; }
  .backdrop-mark {
    position: absolute; left: 200px; top: 330px;
    width: 300px; height: 300px; background: var(--accent-faint);
  }
  .address {
    position: absolute; left: 0; right: 0; top: 1010px;
    text-align: center;
    font-family: "Questrial", sans-serif;
    font-variant: small-caps; letter-spacing: 1.6px;
    font-size: 11px; line-height: 18px; color: var(--ink);
  }
</style>
</head>
<body>
  <main class="letterhead">
    <div class="brand">
      <div class="brand-square"></div>
      <div class="brand-name">Lintel<br>Design</div>
    </div>

    <div class="contact">
      <p class="contact-name">John Smith</p>
      <p class="contact-role">Deisgnation</p>
      <p class="contact-line">(123) 456-7890
        <svg viewBox="0 0 10 10"><path d="M3 1 L4.5 3 L3.6 4 Q4.5 6 6 6.6 L7 5.6 L9 7 L8 9 Q2 8.5 1 2 Z" fill="var(--accent)"/></svg>
      </p>
      <p class="contact-line">info@companyname.com
        <svg viewBox="0 0 10 10"><rect x="0.5" y="2" width="9" height="6.5" fill="var(--accent)"/><path d="M0.8 2.3 L5 5.6 L9.2 2.3" stroke="#fff" stroke-width="0.8" fill="none"/></svg>
      </p>
      <p class="contact-line">companyname.com
        <svg viewBox="0 0 10 10" fill="none" stroke="var(--accent)" stroke-width="0.8"><circle cx="5" cy="5" r="4.3"/><ellipse cx="5" cy="5" rx="2" ry="4.3"/><path d="M0.7 5 H9.3 M1.5 2.8 H8.5 M1.5 7.2 H8.5"/></svg>
      </p>
    </div>

    <div class="header-rule"></div>
    <div class="backdrop-mark"></div>
    <div class="footer-rule"></div>

    <div class="address">
      <p>Address line1, address line2</p>
      <p>country - 123456</p>
    </div>
  </main>
</body>
</html>
```